Business Card Design for Marketing Firm

Looking for business card design for higher end marketing firm. Clean but impressionable/trendy. We are a marketing firm that represents manufacturers in the foodservice equipment and supply industry. Our customers are end users such has hotels, restaurants, country clubs, convention centers and casinos as well as distributors of restaurants supplies and equipment, and manufacturers of foodservice equipment and supplies.
Target Market(s)
Hotels, Restaurants, Supply & Equipment Distributors, Foodservice Manufacturers
Industry/Entity Type
Foodservice/Hospitality
Contact Information for Business Card
Name, Title, Contact Number, Email, Website, Social Media, Address
Requirements
Must have
- Clean & Simple but Serious and Impressionable

```html
<!DOCTYPE html>
<html lang="en">
<head>
<meta charset="utf-8">
<title>Harbor Hospitality Reps – Business Card</title>
<link rel="stylesheet" href="https://fonts.googleapis.com/css2?family=Cinzel:wght@700&family=Arimo:wght@400&display=swap">
<style>
  :root {
    --backdrop: #d9d9db;
    --navy: #020b7a;
    --ink-light: #ffffff;
    --back-ink: #4450c8;
    --rule: rgba(255,255,255,0.75);
  }
  * { margin: 0; padding: 0; box-sizing: border-box; }
  html, body { width: 1200px; height: 800px; overflow: hidden; }
  body {
    background: var(--backdrop);
    font-family: "Arimo", Arial, sans-serif;
    position: relative;
  }
  .card {
    position: absolute;
    top: 240px;
    width: 560px;
    height: 320px;
    border-radius: 24px;
    background: var(--navy);
    color: var(--ink-light);
    overflow: hidden;
  }
  .card--front { left: 25px; }
  .card--back { left: 615px; }

  .social {
    position: absolute; left: 30px; top: 30px;
    display: flex; gap: 6px;
  }
  .social span {
    width: 18px; height: 18px; border-radius: 50%;
    background: var(--ink-light); display: block;
  }
  .brand-name {
    position: absolute; right: 60px; top: 70px;
    font-family: "Arimo", Arial, sans-serif; font-weight: 400;
    font-size: 34px; color: var(--ink-light);
  }
  .identity { position: absolute; left: 128px; top: 148px; }
  .identity .name {
    font-family: "Cinzel", Georgia, serif; font-weight: 700;
    font-size: 22px; letter-spacing: 1px;
  }
  .identity .title { font-size: 15px; margin-top: 2px; }
  .divider {
    position: absolute; left: 128px; right: 40px; top: 200px;
    height: 1px; background: var(--rule);
  }
  .contacts {
    position: absolute; left: 128px; top: 212px;
    list-style: none; font-size: 15px; line-height: 21px;
  }
  .contacts li { display: flex; align-items: center; gap: 8px; }
  .contacts svg { width: 11px; height: 11px; fill: var(--ink-light); }
  .address {
    position: absolute; right: 40px; top: 214px;
    font-size: 15px; line-height: 20px; text-align: left;
  }

  .back-name {
    position: absolute; left: 0; right: 0; top: 142px;
    text-align: center;
    font-family: "Arimo", Arial, sans-serif; font-weight: 400;
    font-size: 30px; line-height: 36px;
    color: var(--back-ink);
  }
</style>
</head>
<body>
  <section class="card card--front" aria-label="Business card front">
    <div class="social" aria-label="Social media links">
      <span></span><span></span><span></span>
    </div>
    <div class="brand-name">Harbor</div>
    <div class="identity">
      <div class="name">OWEN CARTER</div>
      <div class="title">President</div>
    </div>
    <div class="divider"></div>
    <ul class="contacts">
      <li><svg viewBox="0 0 12 12"><path d="M2 1h3l1 3-1.5 1a7 7 0 0 0 2.5 2.5L8 6l3 1v3a1 1 0 0 1-1 1A9 9 0 0 1 1 2a1 1 0 0 1 1-1z"/></svg>(555) 0142-7781</li>
      <li><svg viewBox="0 0 12 12"><path d="M1 2h10v8H1z M1 2l5 4 5-4" fill="none" stroke="#fff" stroke-width="1.4"/></svg>name@HARBOR.com</li>
      <li><svg viewBox="0 0 12 12"><circle cx="6" cy="6" r="5"/></svg>www.HARBOR.com</li>
    </ul>
    <div class="address">4127 Linden Avenue<br>Maple Grove, NY 11020</div>
  </section>

  <section class="card card--back" aria-label="Business card back">
    <div class="back-name">Harbor Hospitality Reps</div>
  </section>
</body>
</html>
```